MRT Property - Business Cards

Looking for a business card & general letterhead, signage etc design for our new logo.

Colours:
000a20
0056a2
00b5ef
0088ce
68cef2

Fonts:
Poppins
Karla

Please keep look and feel of new brand - example in the zip package I sent.

```html
<!DOCTYPE html>
<html lang="en">
<head>
<meta charset="utf-8">
<title>MRT Property – Business Cards</title>
<link rel="stylesheet" href="https://fonts.googleapis.com/css2?family=Poppins:wght@400;500;600;700&display=swap">
<style>
  :root {
    --ink: #000a20;
    --navy: #0056a2;
    --sky: #00b5ef;
    --mid: #0088ce;
    --pale: #68cef2;
    --paper: #ffffff;
    --stage: #b9b9b9;
    --text: #3a3f4a;
    --mist: #f1f5fa;
  }
  * { box-sizing: border-box; margin: 0; padding: 0; }
  html, body { width: 1200px; height: 900px; overflow: hidden; }
  body {
    background: var(--stage);
    font-family: "Poppins", sans-serif;
    position: relative;
  }
  .card {
    position: absolute;
    width: 620px;
    height: 354px;
    border-radius: 26px;
    overflow: hidden;
  }
  .card--front {
    left: 90px; top: 80px;
    background: linear-gradient(180deg, var(--sky) 0%, var(--mid) 55%, var(--navy) 100%);
    display: flex; align-items: center; justify-content: center;
  }
  .card--back {
    left: 490px; top: 466px;
    background: var(--paper);
  }
  .wordmark {
    font-weight: 700;
    font-size: 58px;
    letter-spacing: 1px;
    line-height: 1;
  }
  .card--front .wordmark { color: var(--paper); }
  .card--back .wordmark {
    position: absolute; left: 56px; top: 58px;
    font-size: 46px;
    color: var(--navy);
  }
  .back-glow {
    position: absolute; right: -120px; top: -60px;
    width: 420px; height: 420px; border-radius: 50%;
    background: var(--mist);
  }
  .person { position: absolute; left: 56px; top: 150px; }
  .person__name {
    font-weight: 700; font-size: 24px; color: var(--navy);
    text-transform: uppercase; letter-spacing: 0.5px; line-height: 1.1;
  }
  .person__role { font-size: 16px; color: var(--text); }
  .contact { position: absolute; left: 56px; top: 222px; list-style: none; }
  .contact__item {
    display: flex; align-items: center; gap: 10px;
    font-size: 16px; color: var(--text); line-height: 1.6;
  }
  .contact__item svg { width: 16px; height: 16px; fill: var(--navy); flex: none; }
  .contact__web span { color: var(--navy); }
  .address {
    position: absolute; right: 44px; top: 150px;
    text-align: right; font-size: 15px; color: var(--text); line-height: 1.4;
    font-style: normal;
  }
</style>
</head>
<body>
  <section class="card card--front" aria-label="Business card front">
    <p class="wordmark">MRT Property</p>
  </section>

  <section class="card card--back" aria-label="Business card back">
    <div class="back-glow"></div>
    <p class="wordmark">MRT Property</p>
    <div class="person">
      <p class="person__name">Daniel Carter</p>
      <p class="person__role">Managing Director</p>
    </div>
    <ul class="contact">
      <li class="contact__item">
        <svg viewBox="0 0 16 16" aria-hidden="true"><path d="M3.6 1.2 5.8 3.4c.4.4.4 1 0 1.4L4.7 5.9a8.6 8.6 0 0 0 5.4 5.4l1.1-1.1c.4-.4 1-.4 1.4 0l2.2 2.2c.4.4.4 1 0 1.4l-1.2 1.1C11 16.6 0 5.6 1.1 3.6L2.2 2.4c.4-.4 1-.4 1.4-1.2z"/></svg>
        044-555 018 224
      </li>
      <li class="contact__item">
        <svg viewBox="0 0 16 16" aria-hidden="true"><path d="M1 3h14v10H1z M2 4.2v.4l6 4 6-4v-.4z" fill-rule="evenodd"/></svg>
        hello@mrtproperty.com
      </li>
      <li class="contact__item contact__web">
        <svg viewBox="0 0 16 16" aria-hidden="true"><path d="M8 1a7 7 0 1 0 0 14A7 7 0 0 0 8 1zm0 1.4c.8.8 1.4 2.1 1.6 3.6H6.4C6.6 4.5 7.2 3.2 8 2.4zM2.5 7.2h2.6c0 .6 0 1.1.1 1.6H2.5a5.6 5.6 0 0 1 0-1.6zm4 0h3c.1.5.1 1 0 1.6h-3c-.1-.6-.1-1 0-1.6zm4.4 0h2.6a5.6 5.6 0 0 1 0 1.6h-2.6c.1-.5.1-1 0-1.6zM8 13.6c-.8-.8-1.4-2.1-1.6-3.6h3.2c-.2 1.5-.8 2.8-1.6 3.6z"/></svg>
        <p>www.<span>mrtproperty</span>.com</p>
      </li>
    </ul>
    <address class="address">
      18, Harbour Lane, Suite 4<br>
      20731, Northvale
    </address>
  </section>
</body>
</html>
```